Hunting club needs a new web design !

We need a new web design for our hunting club located in Poland, called "BORYNA". The club was founded in 1945. Colors that we would like to see in the project are the colors of the forest. The website should be built in such a way that all text elements can be changed to another language and can't be graphic.
"BORYNA" means - big, thick forest in which the game, small and big resides

Target Market(s)

hunters,

Industry/Entity Type

Hunting

Coding

Coded - Design and coding required

Number of Pages Required

5+ page

Font styles to use
Decorative

Colors

Designer to choose colors to be used in the design.

Requirements
Must have
• current date, calendar,
• must contain almost all materials from our current web page
• http://boryna-lasowiec.webnest.pl/
• new web address: borynalsw.pl
Nice to have
• current weather in three hunting regions that we allowed to hunt, or indicated by the visitor on the map placed on our web,
• actual phase of the moon, actual moon rising hour, actual moon set hour, actual sun rise hour, actual sun set hour, current weather in region (stalowa wola, poland)
• wood, forest, deers, boars,
Should not have
• mountain photos, modern look, white or bright backgrounds,

```html
<!DOCTYPE html>
<html lang="en">
<head>
<meta charset="utf-8">
<title>Boryna Hunting Club</title>
<link href="https://fonts.googleapis.com/css2?family=Open+Sans:wght@400;600;700;800&display=swap" rel="stylesheet">
<style>
:root{
  --green:#14a82b;
  --brown:#6a4526;
  --brown-dark:#5a3a1f;
  --ink:#444;
  --muted:#666;
  --bar:#f2f2f2;
  --line:#cfcfcf;
  --cal-head:#3b3b3b;
  --white:#fff;
}
*{box-sizing:border-box;margin:0;padding:0}
html,body{width:978px;height:1200px;overflow:hidden}
body{position:relative;background:var(--white);font-family:"Open Sans",sans-serif;color:var(--ink)}
.abs{position:absolute}
.topbar{left:0;top:0;width:978px;height:35px;background:var(--bar)}
.today{right:61px;top:10px;font-size:10.5px;font-weight:700;color:#555;letter-spacing:.3px;display:flex;align-items:center;gap:6px}
.today b{color:var(--brown)}
.brand{left:60px;top:22px;width:118px;height:78px;display:flex;align-items:center;gap:8px;font-size:20px;font-weight:800;color:var(--green)}
.brand i{display:block;width:14px;height:14px;border-radius:50%;background:var(--green)}
.social{right:61px;top:59px;display:flex;gap:20px}
.social span{width:20px;height:20px;border-radius:50%;background:var(--green);display:block}
.nav{left:0;top:106px;width:978px;height:40px;background:var(--brown);display:flex;justify-content:center;align-items:center;gap:24px}
.nav a,.foot-nav a{font-size:11.6px;text-decoration:none;color:var(--white)}
.hero{left:0;top:146px;width:978px;height:335px;background:linear-gradient(135deg,#4c4a3f,#6d6a58 40%,#5b5444 70%,#3f3a30)}
.hero-title{left:0;top:252px;width:978px;text-align:center;color:var(--white);font-size:40px;font-weight:800;letter-spacing:1px}
.hero-sub{left:0;top:302px;width:978px;text-align:center;color:var(--white);font-size:28px;font-weight:700;letter-spacing:.5px}
.btn{background:var(--green);color:var(--white);font-weight:700;font-size:12.5px;letter-spacing:.6px;display:flex;align-items:center;justify-content:center;text-decoration:none}
.hero-btn{left:431px;top:358px;width:116px;height:34px}
.dots{left:464px;top:453px;display:flex;gap:8px}
.dots span{width:7px;height:7px;border-radius:50%;background:var(--white)}
.dots span:first-child{background:var(--green)}
h2{font-size:20.5px;font-weight:700;color:var(--brown);letter-spacing:.6px}
.history-h{left:61px;top:510px}
.history p{font-size:12px;line-height:22px;color:var(--muted);margin-bottom:7px}
.history{left:61px;top:544px;width:340px}
.history-btn{left:61px;top:719px;width:116px;height:34px}
.cal-h{left:428px;top:511px}
.cal{left:428px;top:553px;width:490px;border-collapse:collapse;font-size:12.5px;text-align:center;color:#333}
.cal caption{background:var(--cal-head);color:var(--white);height:29px;line-height:29px;font-size:12.5px}
.cal th{background:#e4e4e4;font-weight:400;font-size:11px;height:28px;border:1px solid var(--line)}
.cal td{height:28.6px;border:1px solid var(--line);background:var(--white)}
.cal td.now{background:var(--green);color:var(--white)}
.band{left:0;top:795px;width:978px;height:308px;background:var(--bar)}
.regions-h{left:61px;top:827px}
.map{left:61px;top:865px;width:220px;height:202px;background:#c9c9c9;border-radius:30px 60px 20px 40px}
.pin{position:absolute}
.region{font-size:11.5px;font-weight:700;color:var(--brown);letter-spacing:.3px}
.wx{display:flex;gap:8px;align-items:center}
.wx b{font-size:11.5px;color:var(--green);line-height:12px;display:block}
.wx small{font-size:9.5px;font-weight:700;color:var(--green);letter-spacing:.6px}
.card{left:430px;width:267px;height:52px;background:linear-gradient(#fff,#f1f1f1);border:1px solid #ccc;display:flex;align-items:center;padding-left:18px;gap:20px}
.card h3{font-size:11.6px;font-weight:700;color:var(--brown);letter-spacing:.2px}
.card p{font-size:11.6px;font-weight:700;color:var(--green)}
.moon{left:721px;top:834px;width:196px;height:233px;background:var(--white)}
.moon-head{height:53px;background:var(--brown);color:var(--white);font-size:20px;font-weight:700;text-align:center;line-height:53px;letter-spacing:.6px;position:relative}
.moon-head::after{content:"";position:absolute;left:86px;bottom:-9px;border:12px solid transparent;border-top-color:var(--brown);border-bottom:0}
.field{display:flex;align-items:center;justify-content:space-between;margin:0 16px 0 15px;height:27px;margin-top:8px;font-size:10.5px;font-weight:600;color:#333}
.field:first-of-type{margin-top:27px}
.select{width:121px;height:27px;background:#eee;display:flex;align-items:center;justify-content:space-between;padding:0 12px 0 10px;font-weight:400;font-size:10px}
.moon-btn{margin:8px 16px 0 16px;height:31px;font-size:10px;letter-spacing:.4px}
.foot-nav{left:0;top:1130px;width:978px;display:flex;justify-content:center;gap:24px}
.foot-nav a{color:#444}
.copy{left:0;top:1158px;width:978px;text-align:center;font-size:11px;color:#555}
</style>
</head>
<body>
<div class="abs topbar"></div>
<div class="abs today">
  <svg width="10" height="10" viewBox="0 0 10 10"><rect x="0.5" y="1.5" width="9" height="8" fill="none" stroke="#777"/><rect x="0.5" y="1.5" width="9" height="2" fill="#777"/></svg>
  TODAY'S DATE: <b>18- 08- 2017</b>
</div>
<div class="abs brand"><i></i>BORYNA</div>
<div class="abs social" aria-label="Social links"><span></span><span></span><span></span><span></span><span></span></div>

<nav class="abs nav">
  <a href="#">Wheel History</a><a href="#">Board of the Wheel</a><a href="#">Hunting Equipment</a><a href="#">Hunting ethics</a><a href="#">Hunting plan</a><a href="#">Hunting calendar</a><a href="#">Cynology</a><a href="#">News</a><a href="#">Gallery</a>
</nav>

<div class="abs hero" role="img" aria-label="Club members in hunting jackets gathered outdoors in winter"></div>
<div class="abs hero-title">WELCOME TO BORYNA</div>
<div class="abs hero-sub">We are a hunting club located in Poland.</div>
<a class="abs btn hero-btn" href="#">READ MORE</a>
<div class="abs dots"><span></span><span></span><span></span><span></span></div>

<h2 class="abs history-h">COMPANY HISTORY</h2>
<div class="abs history">
  <p>Aliquam molestie, mi et imperdiet euismod, dui purus auctor tellus, et interdum lacus lectus et ante. Sed accumsan sollicitudin sapien, sit amet adipiscing turpis gravida ac. In congue, neque ac lobortis volutpat, libero mauris varius mi, vitae suscipit ipsum ligula vitae risus.</p>
  <p>Vestibulum vel metus sit amet turpis bibendum tincidunt vel sit amet quam.</p>
</div>
<a class="abs btn history-btn" href="#">READ MORE</a>

<h2 class="abs cal-h">HUNTING CALENDAR</h2>
<table class="abs cal">
  <caption>August 2017</caption>
  <tr><th>M</th><th>T</th><th>W</th><th>T</th><th>F</th><th>S</th><th>S</th></tr>
  <tr><td></td><td>1</td><td>2</td><td>3</td><td>4</td><td>5</td><td>6</td></tr>
  <tr><td>7</td><td>8</td><td>9</td><td>10</td><td>11</td><td>12</td><td>13</td></tr>
  <tr><td>14</td><td>15</td><td>16</td><td>17</td><td class="now">18</td><td>19</td><td>20</td></tr>
  <tr><td>21</td><td>22</td><td>23</td><td>24</td><td>25</td><td>26</td><td>27</td></tr>
  <tr><td>28</td><td>29</td><td>30</td><td>31</td><td></td><td></td><td></td></tr>
</table>

<div class="abs band"></div>
<h2 class="abs regions-h">HUNTING REGIONS</h2>
<div class="abs map" role="img" aria-label="Map of Poland divided into grey regions"></div>
<svg class="abs" style="left:0;top:0" width="978" height="1200" aria-hidden="true">
  <defs>
    <g id="pin"><path d="M6 0a6 6 0 0 1 6 6c0 5-6 11-6 11S0 11 0 6a6 6 0 0 1 6-6z" fill="#14a82b"/><circle cx="6" cy="6" r="2.4" fill="#fff"/></g>
    <g id="wx"><circle cx="9" cy="9" r="7" fill="#f6b81b"/><path d="M8 20a5 5 0 0 1 2-9 6 6 0 0 1 11 2 4 4 0 0 1 0 7z" fill="#9eb3c9"/></g>
  </defs>
  <use href="#pin" x="184" y="886"/><use href="#pin" x="172" y="966"/><use href="#pin" x="193" y="1035"/>
  <g stroke="#777" fill="none" stroke-width="1"><path d="M202 895 L255 870 H295 M290 866 l5 4 -5 4"/><path d="M190 975 L235 948 H272 M267 944 l5 4 -5 4"/><path d="M211 1044 L255 1016 H292 M287 1012 l5 4 -5 4"/></g>
  <use href="#wx" x="302" y="883"/><use href="#wx" x="280" y="962"/><use href="#wx" x="301" y="1031"/>
  <g transform="translate(448 842)"><use href="#wx"/></g>
  <g transform="translate(448 902)"><use href="#wx"/></g>
  <g transform="translate(448 962)"><path d="M4 18a5 5 0 0 1 3-8 6 6 0 0 1 10 1 4 4 0 0 1 0 7z" fill="none" stroke="#8aa3bb" stroke-width="1.5"/><circle cx="22" cy="14" r="5" fill="#f6b81b"/></g>
  <g transform="translate(448 1022)"><circle cx="15" cy="9" r="7" fill="#f6b81b"/><path d="M2 22a5 5 0 0 1 3-8 6 6 0 0 1 11 2 4 4 0 0 1 0 6z" fill="#bcd3e6"/></g>
</svg>
<div class="abs region" style="left:303px;top:862px">POLAND</div>
<div class="abs wx" style="left:341px;top:884px"><span><b>50 °</b><small>SUNNY</small></span></div>
<div class="abs region" style="left:282px;top:940px">KATOWISE</div>
<div class="abs wx" style="left:319px;top:963px"><span><b>78 °</b><small>SUNNY</small></span></div>
<div class="abs region" style="left:303px;top:1010px">STALOWA WOLA</div>
<div class="abs wx" style="left:340px;top:1032px"><span><b>78 °</b><small>SUNNY</small></span></div>

<div class="abs card" style="top:834px"><span style="width:36px"></span><div><h3>Actual Moon Rising Hour</h3><p>5:10:21am</p></div></div>
<div class="abs card" style="top:894px"><span style="width:36px"></span><div><h3>Actual Moon Set Hour</h3><p>5:10:21am</p></div></div>
<div class="abs card" style="top:954px"><span style="width:36px"></span><div><h3>Actual Sun Rising Hour</h3><p>5:10:21am</p></div></div>
<div class="abs card" style="top:1014px"><span style="width:36px"></span><div><h3>Actual Sun Set Hour</h3><p>5:10:21am</p></div></div>
<svg class="abs" style="left:0;top:0;pointer-events:none" width="978" height="1200" aria-hidden="true">
  <g transform="translate(448 842)"><circle cx="9" cy="9" r="7" fill="#f6b81b"/><path d="M8 22a5 5 0 0 1 2-9 6 6 0 0 1 11 2 4 4 0 0 1 0 7z" fill="#9eb3c9"/></g>
  <g transform="translate(448 902)"><circle cx="9" cy="9" r="7" fill="#f6b81b"/><path d="M8 22a5 5 0 0 1 2-9 6 6 0 0 1 11 2 4 4 0 0 1 0 7z" fill="#9eb3c9"/></g>
  <g transform="translate(442 966)"><path d="M4 20a5 5 0 0 1 3-8 6 6 0 0 1 10 1 4 4 0 0 1 0 7z" fill="none" stroke="#8aa3bb" stroke-width="1.5"/><circle cx="28" cy="14" r="5" fill="#f6b81b"/></g>
  <g transform="translate(446 1024)"><circle cx="17" cy="9" r="7" fill="#f6b81b"/><path d="M2 24a5 5 0 0 1 3-8 6 6 0 0 1 11 2 4 4 0 0 1 0 6z" fill="#bcd3e6"/></g>
</svg>

<div class="abs moon">
  <div class="moon-head">MOON PHASES</div>
  <div class="field">Year:<span class="select">2014<span>⌄</span></span></div>
  <div class="field">Month:<span class="select">Select<span>⌄</span></span></div>
  <div class="field">Day:<span class="select">Select<span>⌄</span></span></div>
  <a class="btn moon-btn" href="#">SHOW PHASES OF THE MOON</a>
</div>

<nav class="abs foot-nav">
  <a href="#">Wheel History</a><a href="#">Board of the Wheel</a><a href="#">Hunting Equipment</a><a href="#">Hunting ethics</a><a href="#">Hunting plan</a><a href="#">Hunting calendar</a><a href="#">Cynology</a><a href="#">News</a><a href="#">Gallery</a>
</nav>
<div class="abs copy">Copyright © 2017. Company Name.All Right Reserved</div>
</body>
</html>
```